website design + images

We need a very appealing website design, layout and images for a sales analytics and sales productivity services company based in San Ramon, California. We need a good design for the home page and a template for all other pages (total 2 designs), and images for all inner pages (center column/banner images, and right hand top corner small images). There are about 18 inner pages.
Updates

Our existing website is www.brightvale.com
Our corporate colours are the ones that are there on the website. The logo is also shown. We will be changing the tagline to "accelerating revenue" or equivalent of that.

Please use the document "website for brightvale - template v2.doc" that I just uploaded for any reference to the content, navigation and wireframes. A few more clarifications are provided mainly for the link "Solutions".

Rajesh Kothuri

Hi,
We just uploaded ver 4 of the website template. There is more elaboration provided around the sublinks / sections for Solutions. Pls review and do get back if you need any clarifications.

Rgds
Rajesh Kothuri

Hi all,
We have so far received a few good designs. The designs are more or less on the right track. I would like to urge all of you to use the content and navigation provided in the document attached to our brief "website for brightvale - template v4.doc".  Please DO NOT use the content in our existing website www.brightvale.com . That is very old. We mentioned it only for reference to colour theme and broad details.

We have totally 13 sections in Solutions pages. They may be designed as a tree of links - first level sublinks - second level sublinks or links - first level sublinks and the remaining as sections within the first level sublinks pages. The page design would remain the same for all inner pages except careers. But after finalizing the design for the inner page, we will need images for the different inner pages.

Rgds
Rajesh Kothuri

Hi,
Thank you all for participation and very good designs. We are quite happy with what we have seen. We have now shortlisted about 4 vendors and sending invididual feedback to them for further improvement. We will be finalizing by Monday or Tuesday.  To the vendors who do not get feedback from us, thank you very much for participation. We may still do business in future for some of our other needs. 
The following are the process steps / expectations going forward, 
1. Feedback to the shortlisted designers and inviting improvements.
2. Review of the improved designs and further shortlist & feedback or direct finalization.
3. The design should be in 1024*768
2. Number of page designs = 2 (home page, inner page).
4. Home page design: instead of delivery model and customers, show one link "Why Us".
4. Solutions page design:  We will be needing an image in center column of solutions page that in a nutshell gives all the different types of solutions we provide. The entire set of solutions is in our attached document website for brightvale - template v4 and I am just uploading v5 with more description on sublinks.
5. After selection, we will be needing images for all the solution pages (total 12 pages under solutions + one solutions page), 1 image for Why Us?, 1 for Careers, and 3 for company (about us/ team, core values, ...) = total 18

Rgds
Rajesh Kothuri

Target Market(s)

We are a sales analytics and sales productivity services company. We help B2B companies with: sales planning; sales operations and sales measurement. The characteristics of our customers are:
- B2B medium enterprises (USD 100M- USD 2B in revenue) in the US
- Primary target verticals are: high-tech, engineering and professional services firms
- Our primary target customers titles are VP of Sales or VP of marketing; we could be selling to the CEO at companies with revenues below $200M

Industry/Entity Type

Consulting

Requirements
Must have
• - Clean, uncluttered design
• - Easy navigation; minimum clicks
Nice to have
• We have already built a content management system and wireframes for this site. To the extent possible, it would be great to leverage the wireframe structure we built, provided you don’t have to compromise on the look and feel and navigation of the site. Below is what we currently have as banner sizes and resolutions are:
• Home page banner size: 950 * 250’
• All pages – center top - image size: 558 * 160
• All pages – right hand top image – 175*135’

```html
<!DOCTYPE html>
<html lang="en">
<head>
<meta charset="utf-8">
<title>Brightvale – Accelerating revenue</title>
<link href="https://fonts.googleapis.com/css2?family=Open+Sans:wght@400;600;700&family=Roboto+Condensed:wght@700&family=Arimo:ital,wght@0,400;1,700&display=swap" rel="stylesheet">
<style>
:root{
  --blue:#0a6db5;
  --blue-dark:#045a9c;
  --green:#4d9a3e;
  --green-dark:#3c8330;
  --text:#1b1b1b;
  --white:#ffffff;
  --grey-bg:#9c9c9c;
  --card-border:#e2e2e2;
}
*{margin:0;padding:0;box-sizing:border-box}
html,body{width:1200px;height:825px;overflow:hidden}
body{
  position:relative;
  font-family:"Arimo",Arial,sans-serif;
  color:var(--text);
  background:linear-gradient(to bottom,#ffffff 0,#ffffff 170px,#d8d8d8 420px,var(--grey-bg) 825px);
}
.topbar{position:absolute;left:0;top:0;width:1200px;height:42px;background:linear-gradient(to bottom,#1584cc,var(--blue))}
.utility{position:absolute;left:54px;top:0;display:flex;height:42px;align-items:center;font-family:"Open Sans",sans-serif;font-size:13px;color:var(--white);letter-spacing:-.2px}
.utility a{display:flex;align-items:center;gap:7px;color:var(--white);text-decoration:none;margin-right:20px}
.utility .signin{height:50px;align-self:flex-start;padding:0 9px;background:linear-gradient(to bottom,#63b04f,var(--green-dark));border-radius:0 0 5px 5px;box-shadow:0 1px 2px rgba(0,0,0,.35);margin-right:12px}
.utility .ico{width:18px;height:18px;border-radius:50%;background:var(--white);display:flex;align-items:center;justify-content:center}

.page{position:absolute;left:48px;top:170px;width:1090px;height:613px;background:var(--white);border-radius:0 0 12px 12px}

.brand{position:absolute;left:62px;top:118px;display:flex;align-items:center;gap:10px;font-family:"Open Sans",sans-serif;font-size:28px;font-weight:600;color:var(--blue-dark)}
.brand .dot{width:16px;height:16px;border-radius:50%;background:var(--blue-dark)}

.mainnav{position:absolute;right:75px;top:113px;display:flex;align-items:center;font-weight:700;font-size:14px;color:var(--blue)}
.mainnav a{color:var(--blue);text-decoration:none;letter-spacing:.4px}
.mainnav .sep{margin:0 9px}
.mainnav .current{background:linear-gradient(to bottom,#5fb34a,var(--green-dark));color:var(--white);padding:3px 15px;border-radius:12px;border:1px solid #2f6d25;margin-right:12px}

.hero{position:absolute;left:59px;top:180px;width:1068px;height:281px;overflow:hidden;
  background:linear-gradient(100deg,#0c6db8 0,#1680cc 35%,#6cb8ea 55%,#e8f3fb 66%,#f3f3f3 100%);
  box-shadow:0 0 18px rgba(0,0,0,.25)}
.hero-swoosh{position:absolute;left:0;top:0}
.hero-photo{position:absolute;left:570px;top:0;width:498px;height:281px;background:linear-gradient(160deg,#e9ecef 0,#c7b69a 45%,#8d7a62 80%,#d9dadb 100%);opacity:.9}
.hero-title{position:absolute;left:24px;top:115px;font-family:"Open Sans",sans-serif;color:var(--white)}
.hero-title h1{font-size:31px;font-weight:600;letter-spacing:-.3px;line-height:36px}
.hero-title p{font-size:19px;font-weight:600;line-height:25px;letter-spacing:-.2px}
.pager{position:absolute;left:26px;top:234px;display:flex;gap:5px}
.pager span{width:20px;height:20px;border:1px solid #bfbfbf;border-radius:3px;background:#f2f2f2;color:#555;font-size:11px;display:flex;align-items:center;justify-content:center;font-family:Arial,sans-serif}
.pager .on{background:var(--blue-dark);color:var(--white);border-color:#d7e8f5}

.welcome{position:absolute;left:64px;top:481px;width:472px}
.welcome h2{font-family:"Open Sans",sans-serif;font-size:22px;font-weight:700;color:var(--green);letter-spacing:-.3px;margin-bottom:4px}
.welcome p{font-size:13.2px;line-height:19px;padding-left:4px}

.service{position:absolute;top:482px;width:186px;height:173px;border:1px solid var(--card-border);border-radius:8px;background:var(--white);box-shadow:0 0 4px rgba(0,0,0,.08)}
.service .thumb{position:absolute;left:8px;top:8px;width:168px;height:78px}
.service .label{position:absolute;left:8px;top:86px;width:168px;height:46px;background:var(--green);color:var(--white);font-family:"Roboto Condensed",sans-serif;font-weight:700;font-size:14px;line-height:15px;padding:9px 9px 0}
.service .more{position:absolute;left:8px;top:141px;width:65px;height:22px;border:1px solid #9a9a9a;border-radius:4px;background:linear-gradient(#fafafa,#d9d9d9);font-style:italic;font-weight:700;font-size:10.5px;color:#444;display:flex;align-items:center;justify-content:center}
.s1{left:550px}.s2{left:745px}.s3{left:940px}
.s1 .thumb{background:linear-gradient(135deg,#3b3f46,#9aa1a8 55%,#e6e6e6)}
.s2 .thumb{background:linear-gradient(135deg,#2a5c8c,#b9cde0 50%,#efe9e2)}
.s3 .thumb{background:linear-gradient(180deg,#dfe9f2,#f7f7f7)}

.divider{position:absolute;left:90px;top:672px;width:1020px;height:10px;background:radial-gradient(ellipse at center top,rgba(0,0,0,.22),rgba(0,0,0,0) 70%)}

.testimonial{position:absolute;left:64px;top:694px;width:1064px}
.testimonial h3{display:flex;align-items:center;gap:5px;font-family:"Open Sans",sans-serif;font-size:14.5px;font-weight:700;color:var(--blue-dark);letter-spacing:-.2px}
.testimonial p{margin-top:8px;font-size:13.2px;line-height:19px;padding-left:1px}
.testimonial cite{font-style:italic;font-weight:700}

.footer{position:absolute;top:791px;left:58px;width:1066px;display:flex;justify-content:space-between;font-size:13.5px;color:var(--white)}
.footer a{color:var(--white);text-decoration:none}
</style>
</head>
<body>
<header class="topbar">
  <nav class="utility">
    <a class="signin" href="#"><span class="ico"><svg width="10" height="10" viewBox="0 0 10 10"><rect x="1" y="1" width="7" height="8" fill="none" stroke="#3c8330" stroke-width="1.3"/><path d="M0 5h5M3.5 3l2 2-2 2" stroke="#3c8330" stroke-width="1.3" fill="none"/></svg></span>SIGN IN / REGISTER</a>
    <a href="#"><span class="ico"><svg width="11" height="11" viewBox="0 0 11 11"><rect x="3.5" y="1" width="4" height="3" fill="none" stroke="#3c8330"/><rect x="0.5" y="7" width="4" height="3" fill="none" stroke="#3c8330"/><rect x="6.5" y="7" width="4" height="3" fill="none" stroke="#3c8330"/><path d="M5.5 4v1.5M2.5 7V5.5h6V7" stroke="#3c8330" fill="none"/></svg></span>CONTACT &nbsp;US</a>
    <a href="#"><span class="ico"><svg width="11" height="9" viewBox="0 0 11 9"><rect x="0.5" y="0.5" width="10" height="8" fill="none" stroke="#3c8330"/><path d="M0.5 0.5l5 4 5-4" stroke="#3c8330" fill="none"/></svg></span>SITEMAP</a>
  </nav>
</header>

<div class="page"></div>

<div class="brand"><span class="dot"></span>Brightvale</div>

<nav class="mainnav">
  <a class="current" href="#">Home</a>
  <a href="#">Solutions</a><span class="sep">|</span>
  <a href="#">Why Us</a><span class="sep">|</span>
  <a href="#">Company</a><span class="sep">|</span>
  <a href="#">Careers</a>
</nav>

<section class="hero">
  <svg class="hero-swoosh" width="1068" height="281" viewBox="0 0 1068 281">
    <path d="M0 150 C250 80 480 60 700 90 L700 110 C480 85 250 110 0 190Z" fill="#ffffff" opacity=".12"/>
    <path d="M0 240 C300 170 520 170 700 200 L700 215 C520 190 300 200 0 270Z" fill="#ffffff" opacity=".1"/>
  </svg>
  <div class="hero-photo" role="img" aria-label="Photo of three business colleagues reviewing documents at a laptop"></div>
  <div class="hero-title">
    <h1>Do more with less.</h1>
    <p>No upfront software, hardware,<br>people or training costs for you. Pay as you go.</p>
  </div>
  <div class="pager"><span>1</span><span class="on">2</span><span>3</span></div>
</section>

<section class="welcome">
  <h2>Welcome to Brightvale</h2>
  <p>At Brightvale, we deliver solutions to improve sales productivity and marketing effectiveness of high-tech, engineering, and professional services firms. Our customers lead corporate marketing, product marketing, channel marketing, sales operations, sales management and IT functions at their organizations. We are a collection of deeply passionate people who take immense pride in what we do, exemplified by our mantra: “Expect More.” We encourage our customers to expect more of us, while we continue to expect more of each other.</p>
</section>

<article class="service s1">
  <div class="thumb" role="img" aria-label="Photo of hands reviewing sales charts with a pen"></div>
  <div class="label">Sales Planning<br>Analytics</div>
  <div class="more">READ ON</div>
</article>
<article class="service s2">
  <div class="thumb" role="img" aria-label="Photo of support staff wearing headsets"></div>
  <div class="label">Sales Operations<br>Support</div>
  <div class="more">READ ON</div>
</article>
<article class="service s3">
  <div class="thumb">
    <svg width="168" height="78" viewBox="0 0 168 78" role="img" aria-label="Rising bar chart">
      <g fill="#e0623a">
        <rect x="18" y="52" width="14" height="26"/><rect x="40" y="42" width="14" height="36"/><rect x="62" y="46" width="14" height="32"/><rect x="84" y="30" width="14" height="48"/><rect x="106" y="22" width="14" height="56"/><rect x="128" y="10" width="14" height="68"/>
      </g>
    </svg>
  </div>
  <div class="label">Sales Measurement<br>Analytics</div>
  <div class="more">READ ON</div>
</article>

<div class="divider"></div>

<section class="testimonial">
  <h3><svg width="22" height="20" viewBox="0 0 22 20"><ellipse cx="11" cy="9" rx="10" ry="8" fill="#1e86d0"/><ellipse cx="9" cy="6" rx="6" ry="3" fill="#8fcaf2"/><path d="M5 15l-2 5 6-3z" fill="#1e86d0"/></svg>Customer Testimonial</h3>
  <p>Lorem ipsum dolor sit amet, consectetur adipiscing elit. Pellentesque hendrerit leo vel sem iaculis eu tincidunt nulla consectetur. Class aptent taciti sociosqu ad litora torquent per conubia nostra, per inceptos himenaeos. Aliquam ornare dignissim consequat. <cite>Daniel, Manager - Norland Systems</cite></p>
</section>

<footer class="footer">
  <div><a href="#">Contact Us</a> | <a href="#">Sitemap</a> &nbsp;| &nbsp;<a href="#">Disclaimer</a></div>
  <div>© 2010. Brightvale, Inc. All Rights Reserved</div>
</footer>
</body>
</html>
```